CopperWanderer Stretching and Strength

We need a application design for a our first IOS application. the goal of the application is to categorize stretching and strength routines for triathlon.

We would like to see designs that use the color orange.

The design of the application should be compliant with the last version of the IOS Mobile.

For this first design we need the folowing pages:

1- Sign up
2- Log in
3- Home
4- View Exercises
5- Do it
6- Profile

The description of each page is in the attached document.

We need a logo design for the application. The logo should express that mission of the application that is for stretch and strength training for Triathlon.

We will use https://pellavokit.example to develop the application, if you have any experience of the limitation that this technology have it will be a plus.

If you have any question please feel free to contact us.

Reason: We will extend the deadline to be sure that we select the best design from all of you. we will take the final decision next Tuesday.

Target Market(s)

The market for my aplicación is the Running a Triathlon world.

Logo Text

CopperWanderer

Font styles to use
Serif

Colors
f37122
ffffff
dcdcdc

Requirements
Must have
• In some future we will add more features in the menu. We should considere it for the design.
• The designs should include all the screens in the power point.

```html
<!DOCTYPE html>
<html lang="en">
<head>
<meta charset="utf-8">
<title>CopperWanderer – Sign Up</title>
<link href="https://fonts.googleapis.com/css2?family=Roboto:wght@300;400;500;700&display=swap" rel="stylesheet">
<style>
  :root {
    --orange: #f37122;
    --white: #ffffff;
    --field-bg: #ffffff;
    --screen-bg: #e9edf1;
    --page-bg: #d6e4f0;
    --text-muted: #6f6f6f;
    --icon-grey: #8a8a8a;
    --social-blue: #1c60b8;
    --social-grey: #b3b3b3;
  }
  * { box-sizing: border-box; margin: 0; padding: 0; }
  html, body {
    width: 1200px; height: 1200px; overflow: hidden;
    background: var(--page-bg);
    font-family: 'Roboto', Arial, sans-serif;
  }
  .screen {
    position: absolute; left: 274px; top: 20px;
    width: 652px; height: 1160px;
    background: var(--screen-bg);
    overflow: hidden;
  }
  .header {
    position: absolute; left: 0; top: 0; width: 100%; height: 300px;
    background: var(--orange); color: var(--white);
  }
  .status-bar {
    position: absolute; left: 0; top: 10px; width: 100%; height: 30px;
    font-size: 19px; display: flex; align-items: center;
  }
  .status-left { position: absolute; left: 10px; display: flex; align-items: center; gap: 6px; }
  .status-time { position: absolute; left: 0; width: 100%; text-align: center; }
  .status-right { position: absolute; right: 10px; display: flex; align-items: center; gap: 8px; }
  .back-button { position: absolute; left: 14px; top: 68px; }
  .add-photo {
    position: absolute; left: 0; top: 122px; width: 100%;
    text-align: center; font-size: 18px; font-weight: 300; letter-spacing: 0.2px;
  }
  .add-photo svg { display: block; margin: 0 auto 10px; }
  .field {
    position: absolute; height: 65px; background: var(--field-bg);
    box-shadow: 0 2px 3px rgba(0,0,0,0.12);
    display: flex; align-items: center; justify-content: space-between;
    padding: 0 24px; font-size: 24px; color: var(--text-muted);
  }
  .field-full { left: 44px; width: 562px; }
  .field-age { left: 44px; width: 276px; }
  .field-gender { left: 329px; width: 277px; }
  .receive-email {
    position: absolute; left: 44px; top: 810px;
    display: flex; align-items: center; gap: 16px;
    font-size: 21px; color: var(--text-muted);
  }
  .create-account {
    position: absolute; left: 44px; top: 877px; width: 562px; height: 71px;
    border-radius: 36px; background: var(--orange); color: var(--white);
    box-shadow: 0 3px 4px rgba(0,0,0,0.15);
    display: flex; align-items: center; justify-content: center;
    font-size: 26px; font-weight: 500;
  }
  .login-prompt {
    position: absolute; left: 0; top: 972px; width: 100%; text-align: center;
    font-size: 20px; color: var(--text-muted);
  }
  .login-prompt .login-link { color: var(--orange); text-decoration: underline; font-weight: 500; }
  .divider-or {
    position: absolute; left: 311px; top: 1019px; width: 30px; height: 30px;
    border-radius: 50%; background: #dde1e5;
    display: flex; align-items: center; justify-content: center;
    font-size: 13px; font-weight: 500; color: #444;
  }
  .social-bar { position: absolute; left: 0; top: 1081px; width: 100%; height: 79px; display: flex; }
  .social-button {
    width: 50%; height: 100%; display: flex; align-items: center; justify-content: center; gap: 14px;
    font-size: 23px;
  }
  .social-circlenet { background: var(--social-blue); color: var(--white); }
  .social-postmail { background: var(--white); color: #333; }
  .social-dot { width: 46px; height: 46px; border-radius: 50%; flex: none; }
  .social-circlenet .social-dot { background: var(--white); }
  .social-postmail .social-dot { background: var(--social-grey); }
</style>
</head>
<body>
<main class="screen">
  <header class="header">
    <div class="status-bar">
      <div class="status-left">
        <svg width="56" height="12" viewBox="0 0 56 12"><g fill="#fff"><circle cx="6" cy="6" r="5"/><circle cx="17" cy="6" r="5"/><circle cx="28" cy="6" r="5"/></g><g fill="none" stroke="#fff" stroke-width="1"><circle cx="39" cy="6" r="4.5"/><circle cx="50" cy="6" r="4.5"/></g></svg>
        <span>VELLO</span>
        <svg width="20" height="16" viewBox="0 0 20 16"><path d="M10 15 L2 6 A11 11 0 0 1 18 6 Z" fill="#fff"/></svg>
      </div>
      <div class="status-time">4:21 PM</div>
      <div class="status-right">
        <svg width="12" height="20" viewBox="0 0 12 20" fill="none" stroke="rgba(255,255,255,0.7)" stroke-width="1.4"><path d="M2 5 L10 14 L6 18 V2 L10 6 L2 15"/></svg>
        <span>100%</span>
        <svg width="40" height="16" viewBox="0 0 40 16"><rect x="1" y="1" width="34" height="14" rx="3" fill="#fff"/><rect x="36" y="5" width="3" height="6" rx="1" fill="#fff"/></svg>
      </div>
    </div>
    <svg class="back-button" width="32" height="24" viewBox="0 0 32 24" fill="none" stroke="#fff" stroke-width="2"><path d="M30 12 H3 M12 3 L3 12 L12 21"/></svg>
    <div class="add-photo">
      <svg width="34" height="34" viewBox="0 0 34 34" stroke="#fff" stroke-width="1.5"><path d="M17 2 V32 M2 17 H32"/></svg>
      ADD PHOTO
    </div>
  </header>

  <div class="field field-full" style="top:322px">Full Name
    <svg width="22" height="26" viewBox="0 0 22 26" fill="var(--icon-grey)"><circle cx="11" cy="7" r="6"/><path d="M1 25 C1 16 21 16 21 25 Z"/></svg>
  </div>
  <div class="field field-full" style="top:400px">Email Id
    <svg width="26" height="20" viewBox="0 0 26 20" fill="var(--icon-grey)"><rect x="0" y="0" width="26" height="20" rx="2"/><path d="M1 2 L13 11 L25 2" fill="none" stroke="#fff" stroke-width="2"/></svg>
  </div>
  <div class="field field-age" style="top:478px">Age
    <svg width="26" height="26" viewBox="0 0 26 26" fill="none" stroke="var(--icon-grey)" stroke-width="2"><rect x="2" y="4" width="22" height="20" rx="1"/><path d="M2 10 H24 M8 1 V6 M18 1 V6"/><g fill="var(--icon-grey)" stroke="none"><rect x="6" y="13" width="3" height="3"/><rect x="11" y="13" width="3" height="3"/><rect x="16" y="13" width="3" height="3"/><rect x="6" y="18" width="3" height="3"/><rect x="11" y="18" width="3" height="3"/><rect x="16" y="18" width="3" height="3"/></g></svg>
  </div>
  <div class="field field-gender" style="top:478px">Gender:
    <svg width="18" height="10" viewBox="0 0 18 10" fill="#555"><path d="M0 0 H18 L9 10 Z"/></svg>
  </div>
  <div class="field field-full" style="top:556px">Sport:
    <svg width="18" height="10" viewBox="0 0 18 10" fill="#555"><path d="M0 0 H18 L9 10 Z"/></svg>
  </div>
  <div class="field field-full" style="top:634px">User Name
    <svg width="22" height="26" viewBox="0 0 22 26" fill="var(--icon-grey)"><circle cx="11" cy="7" r="6"/><path d="M1 25 C1 16 21 16 21 25 Z"/></svg>
  </div>
  <div class="field field-full" style="top:712px">Password
    <svg width="22" height="28" viewBox="0 0 22 28" fill="var(--icon-grey)"><path d="M5 12 V8 A6 6 0 0 1 17 8 V12" fill="none" stroke="var(--icon-grey)" stroke-width="3"/><rect x="1" y="12" width="20" height="15" rx="2"/><rect x="10" y="16" width="2" height="6" fill="#fff"/></svg>
  </div>

  <div class="receive-email">
    <svg width="25" height="25" viewBox="0 0 25 25" fill="none" stroke="var(--orange)" stroke-width="1.5"><rect x="1" y="1" width="23" height="23"/><path d="M6 13 L10 17 L19 7"/></svg>
    Receive Email
  </div>

  <div class="create-account">CREATE ACCOUNT</div>

  <p class="login-prompt">You already have an account? <span class="login-link">LOG IN</span> now</p>
  <div class="divider-or">OR</div>

  <div class="social-bar">
    <div class="social-button social-circlenet"><span class="social-dot"></span>Sign up with Circlenet</div>
    <div class="social-button social-postmail"><span class="social-dot"></span>Sign up with Postmail</div>
  </div>
</main>
</body>
</html>
```